Automotive component supplier needs a business card design

We need a business card design for our company called Velran Global Components Ltd based in the UK. We are a supplier of interior and exterior components to premium car manufacturers such as Corvel Ashby, Hadley Fenn, Marquist and Tavarelli. We would like to see a modern business card design that uses the colour blue.

Target Market(s)

Premium automotive car manufacturers.

Industry/Entity Type

Automotive

Contact Information for Business Card

Company Name : Velran Global Components Limited
Address: 17 Marlow Yard, Upper Heath, Warwick, CV31 8QL, United Kingdom
Web Address : www.velrancomponents-example.co.uk

Font styles to use
Other font styles liked:
• Helvetica

Colors
3176b5
0255a3
85acd3
cfdeed
cee9f5
85cae6
34a6d7
0692cd
9bcb3c

Requirements
Must have
• Clear company logo and a mixture of blue colours.
Nice to have
• A high quality modern image.
Should not have
• Multiple colours.

```html
<!DOCTYPE html>
<html lang="en">
<head>
<meta charset="utf-8">
<title>Velran Global Components – Business Card</title>
<link rel="stylesheet" href="https://fonts.googleapis.com/css2?family=Arimo:wght@400;700&display=swap">
<style>
  :root{
    --blue:#0692cd;
    --blue-deep:#0255a3;
    --green:#9bcb3c;
    --ink:#3a3a3a;
    --paper:#ffffff;
    --backdrop:#e6e8ea;
  }
  *{margin:0;padding:0;box-sizing:border-box}
  html,body{width:1200px;height:950px;overflow:hidden}
  body{background:var(--backdrop);font-family:"Arimo",Helvetica,Arial,sans-serif;position:relative}

  .card{position:absolute;left:250px;width:700px;height:400px;box-shadow:0 6px 18px rgba(0,0,0,.18);overflow:hidden}
  .card--front{top:50px;background:var(--paper)}
  .card--back{top:500px;background:var(--green);color:#fff}

  /* front */
  .brand{position:absolute;right:48px;top:34px;text-align:right}
  .brand__name{font-weight:700;font-size:64px;letter-spacing:4px;color:var(--blue);line-height:1}
  .brand__tagline{font-size:15px;letter-spacing:1.5px;color:var(--blue);margin-top:6px}
  .divider{position:absolute;left:48px;right:48px;top:152px;height:1px;background:var(--blue)}
  .address{position:absolute;right:48px;top:170px;text-align:right;font-size:15px;line-height:1.45;color:var(--ink)}
  .person{position:absolute;left:48px;top:222px}
  .person__name{font-size:22px;color:var(--blue);line-height:1.1}
  .person__role{font-size:15px;color:var(--green);margin-top:2px}
  .contacts{list-style:none;margin-top:12px}
  .contacts li{display:flex;align-items:center;gap:10px;font-size:14px;color:var(--ink);line-height:1.55}
  .contacts svg{width:14px;height:14px;flex:none}
  .edge{position:absolute;left:0;right:0;bottom:0;height:14px;background:var(--blue)}
  .edge::before{content:"";position:absolute;left:0;right:0;top:0;height:5px;background:var(--green)}

  /* back */
  .back-brand{position:absolute;left:0;right:0;top:118px;text-align:center}
  .back-brand__name{font-weight:700;font-size:92px;letter-spacing:6px;line-height:1}
  .back-brand__tagline{font-size:20px;letter-spacing:2px;margin-top:10px}
  .back-web{position:absolute;left:0;right:0;bottom:40px;text-align:center;font-size:15px;letter-spacing:3px}
</style>
</head>
<body>

<section class="card card--front" aria-label="Business card front">
  <div class="brand">
    <div class="brand__name">VELRAN</div>
    <div class="brand__tagline">GLOBAL COMPONENTS</div>
  </div>
  <div class="divider"></div>
  <address class="address" style="font-style:normal">
    17 Marlow Yard, Upper Heath<br>
    Warwick, CV31 8QL<br>
    United Kingdom
  </address>

  <div class="person">
    <div class="person__name">Mara Tellick</div>
    <div class="person__role">President</div>
    <ul class="contacts">
      <li>
        <svg viewBox="0 0 16 16" aria-hidden="true"><path fill="var(--blue)" d="M4 1l3 3-2 2c1 2 3 4 5 5l2-2 3 3-2 3C7 15 1 9 1 3z"/></svg>
        555 0142 7731
      </li>
      <li>
        <svg viewBox="0 0 16 16" aria-hidden="true"><rect x="4" y="1" width="8" height="14" rx="1.5" fill="none" stroke="var(--blue)" stroke-width="1.6"/><circle cx="8" cy="12.5" r="1" fill="var(--blue)"/></svg>
        555 0198 2406
      </li>
      <li>
        <svg viewBox="0 0 16 16" aria-hidden="true"><rect x="1" y="3" width="14" height="10" fill="var(--blue)"/><path d="M1 3l7 6 7-6" fill="none" stroke="#fff" stroke-width="1.3"/></svg>
        mara@velrancomponents-example.co.uk
      </li>
      <li>
        <svg viewBox="0 0 16 16" aria-hidden="true"><circle cx="8" cy="8" r="7" fill="var(--blue)"/><path d="M1 8h14M8 1c-3 4-3 10 0 14M8 1c3 4 3 10 0 14" fill="none" stroke="#fff" stroke-width="1"/></svg>
        www.velrancomponents-example.co.uk
      </li>
    </ul>
  </div>
  <div class="edge"></div>
</section>

<section class="card card--back" aria-label="Business card back">
  <div class="back-brand">
    <div class="back-brand__name">VELRAN</div>
    <div class="back-brand__tagline">GLOBAL COMPONENTS</div>
  </div>
  <div class="back-web">www.velrancomponents-example.co.uk</div>
</section>

</body>
</html>
```